Design a Travel and Tourism website

We would like a freelancer to design a website that is essentially easy to use and navigate database providing local information for Travelers about destination countries.

We proposed website would discuss different rates, fees, visa requirement, resort locations, cheap flights, etc. This website should be elegant and modern. Our business name is rovanix.
Some reference websites are zemplorift.ca, brindlefoxhaven.com,
There should be a forum in the website where travell\ers discuss about their first hand tranvel experience to such destinations.

Tourism

```html
<!DOCTYPE html>
<html lang="en">
<head>
<meta charset="utf-8">
<title>Rovanix – Travel and Tourism</title>
<link href="https://fonts.googleapis.com/css2?family=Roboto:wght@300;400;500;700&family=Open+Sans:wght@400;600&display=swap" rel="stylesheet">
<style>
:root{
  --orange:#f7941d;
  --orange-dark:#ef7f0f;
  --green:#8dc63f;
  --ink:#333;
  --body:#777;
  --light:#f4f5f7;
  --line:#e3e3e3;
  --panel:rgba(20,20,20,.72);
  --white:#fff;
  --footer:#fff;
}
*{box-sizing:border-box;margin:0;padding:0}
html,body{width:1200px;height:3396px;overflow:hidden}
body{position:relative;font-family:"Open Sans",sans-serif;color:var(--body);background:var(--white);font-size:11px}
.abs{position:absolute}
h2.section-title{position:absolute;left:0;width:1200px;text-align:center;font-family:"Roboto",sans-serif;font-weight:400;font-size:26px;color:var(--ink)}
h2.section-title span{color:var(--orange)}
.section-intro{position:absolute;left:240px;width:720px;text-align:center;font-size:11px;line-height:20px;color:#666}

/* header */
.site-header{position:absolute;left:0;top:0;width:1200px;height:100px;border-top:4px solid var(--orange);background:var(--white)}
.brand{position:absolute;left:86px;top:28px;display:flex;align-items:center;gap:10px;font-family:"Roboto",sans-serif;font-weight:700;font-size:32px;color:var(--orange)}
.brand i{display:block;width:26px;height:26px;border-radius:50%;background:var(--green)}
.main-nav{position:absolute;right:155px;top:44px;display:flex;gap:46px;font-family:"Roboto",sans-serif;font-size:11.5px;color:#444;font-weight:500}
.search-toggle{position:absolute;left:1073px;top:30px;width:40px;height:40px;border-radius:50%;background:var(--orange)}

/* hero */
.hero{position:absolute;left:0;top:100px;width:1200px;height:563px;background:linear-gradient(180deg,#c7a25a 0%,#8f7a3c 30%,#5d6a52 55%,#3e5564 75%,#2e3f4c 100%)}
.search-panel{position:absolute;left:172px;top:52px;width:858px;height:488px;background:var(--panel)}
.mode-tabs{position:absolute;left:18px;top:18px;display:flex;gap:8px}
.mode-tab{width:78px;height:56px;border:1px solid rgba(255,255,255,.15);background:rgba(255,255,255,.06);color:#fff;font-family:"Roboto",sans-serif;font-size:10px;font-weight:500;text-align:center;padding-top:34px;position:relative}
.mode-tab svg{position:absolute;left:29px;top:10px}
.mode-tab.active{background:var(--orange);border-color:var(--orange)}
.sub-tabs{position:absolute;left:18px;top:102px;display:flex;gap:6px}
.sub-tab{height:34px;padding:0 14px;line-height:34px;color:#fff;font-family:"Roboto",sans-serif;font-size:9.5px;font-weight:500}
.sub-tab.active{background:var(--orange)}
.field-label{position:absolute;color:#fff;font-family:"Roboto",sans-serif;font-weight:500;font-size:11px}
.field{position:absolute;height:36px;background:#fff;border-radius:2px;color:#999;font-size:10.5px;line-height:36px;padding-left:30px}
.field.select{padding-left:14px}
.field.select::after{content:"";position:absolute;right:12px;top:15px;border:4px solid transparent;border-top:5px solid #666}
.field svg{position:absolute;left:10px;top:11px}
.check-row{position:absolute;left:18px;top:313px;color:#fff;font-size:11px;font-family:"Roboto",sans-serif;font-weight:500;display:flex;gap:8px;align-items:center}
.check-row i{width:13px;height:13px;background:#fff;display:block}
.advanced{position:absolute;left:18px;top:345px;color:var(--orange);font-size:10px;font-family:"Roboto",sans-serif;font-weight:500}
.search-btn{position:absolute;left:670px;top:416px;width:136px;height:46px;background:var(--orange);color:#fff;font-family:"Roboto",sans-serif;font-weight:500;font-size:13px;text-align:center;line-height:46px}

/* welcome */
.feature{position:absolute;top:838px;width:320px;text-align:center}
.feature h3{font-family:"Roboto",sans-serif;font-weight:500;font-size:16px;color:var(--orange);margin-top:22px}
.feature p{font-size:11px;line-height:22px;color:#666;margin-top:12px;padding:0 8px}
.feature svg{display:block;margin:0 auto}

/* destinations */
.destinations{position:absolute;left:0;top:1082px;width:1200px;height:621px;background:var(--light)}
.card{position:absolute;background:#fff;box-shadow:0 1px 4px rgba(0,0,0,.08)}
.card .photo{position:absolute;left:10px;top:10px;right:10px}
.card h4{position:absolute;left:10px;font-family:"Roboto",sans-serif;font-weight:500;font-size:14px;color:var(--ink)}
.card p{position:absolute;left:10px;right:10px;font-size:10.5px;line-height:19px;color:#777}
.stars{position:absolute;right:12px;display:flex;gap:2px}
.stars i{width:9px;height:9px;border:1px solid var(--orange);border-radius:50%;display:block}
.stars i.on{background:var(--orange)}
.meta{position:absolute;left:10px;right:10px;display:flex;justify-content:space-between;font-size:10.5px;color:#777;border-top:1px solid var(--line);padding-top:18px}
.meta span{display:flex;align-items:center;gap:6px}
.meta b{color:var(--orange);font-weight:600}

/* banner */
.banner{position:absolute;left:0;top:1703px;width:1200px;height:398px;background:linear-gradient(100deg,#d9c7b0 0%,#8fb9d6 40%,#3f9fd3 70%,#2b8cc7 100%)}
.banner h3{position:absolute;right:88px;top:134px;text-align:right;font-family:"Roboto",sans-serif;color:#fff}
.banner .kicker{font-weight:300;font-size:34px;letter-spacing:.5px;display:block}
.banner .headline{font-weight:500;font-size:40px;display:block;margin-top:6px}
.banner .tour-btn{position:absolute;left:750px;top:258px;width:190px;height:46px;border:1px solid #fff;color:#fff;text-align:center;line-height:44px;font-family:"Roboto",sans-serif;font-weight:500;font-size:13px}

/* testimonial */
.quote{position:absolute;left:177px;top:2738px;width:545px;font-size:11px;line-height:22px;color:#666}
.quote-mark{position:absolute;font-family:Georgia,serif;font-size:34px;color:#aaa}
.quote-name{position:absolute;left:177px;top:2872px;font-family:"Roboto",sans-serif;font-weight:500;color:var(--orange);font-size:12px}
.quote-date{position:absolute;left:177px;top:2893px;font-size:10.5px;color:#777}
.avatar{position:absolute;left:774px;top:2721px;width:196px;height:196px;border-radius:50%;border:6px solid #ececec;background:radial-gradient(circle at 50% 45%,#d8b49b 0%,#a9785c 55%,#6f4a36 100%)}

/* partners */
.partners{position:absolute;left:0;top:2955px;width:1200px;height:117px;background:var(--orange)}
.partner{position:absolute;top:30px;width:132px;height:58px;border:1px solid rgba(255,255,255,.45);color:#fff;font-family:"Roboto",sans-serif;font-weight:500;font-size:17px;display:flex;align-items:center;justify-content:center;gap:8px}
.partner i{width:12px;height:12px;border-radius:50%;background:#fff;display:block}

/* footer */
.site-footer h5{position:absolute;top:3110px;font-family:"Roboto",sans-serif;font-weight:500;font-size:15px;color:var(--ink)}
.link-list{position:absolute;top:3144px;list-style:none;font-size:11px;color:#555}
.link-list li{height:26px;display:flex;align-items:center;gap:10px}
.link-list li::before{content:"";width:0;height:0;border:3px solid transparent;border-left:4px solid #999}
.contact-list{position:absolute;left:276px;top:3142px;list-style:none;font-size:11px;color:#777}
.contact-list li{display:flex;gap:10px;align-items:flex-start;min-height:32px}
.contact-list svg{flex:none;margin-top:2px}
.contact-list a{color:#777}
.subscribe-note{position:absolute;left:774px;top:3144px;font-size:11px;color:#555}
.subscribe{position:absolute;left:774px;top:3178px;display:flex}
.subscribe .email{width:232px;height:36px;border:1px solid #ccc;font-size:11px;line-height:34px;padding-left:12px;color:#333}
.subscribe .go{width:94px;height:36px;background:var(--green);color:#fff;font-family:"Roboto",sans-serif;font-weight:500;font-size:11px;line-height:36px;text-align:center}
.social{position:absolute;left:774px;top:3258px;display:flex;gap:8px}
.social i{width:28px;height:28px;border-radius:50%;background:var(--orange);display:block}
.copyright{position:absolute;left:0;top:3345px;width:1200px;text-align:center;font-size:10.5px;color:#666;border-top:1px solid var(--line);padding-top:12px}
</style>
</head>
<body>

<header class="site-header">
  <div class="brand"><i></i>Rovanix</div>
  <nav class="main-nav"><span>HOME</span><span>TRAVEL</span><span>HOTELS</span><span>CARS</span><span>FLIGHTS</span><span>ABOUT</span><span>CONTACT</span></nav>
  <div class="search-toggle">
    <svg width="40" height="40" viewBox="0 0 40 40"><circle cx="18.5" cy="18.5" r="5" fill="none" stroke="#fff" stroke-width="2"/><line x1="22" y1="22" x2="26" y2="26" stroke="#fff" stroke-width="2"/></svg>
  </div>
</header>

<section class="hero" role="img" aria-label="Autumn trees along a city canal with moored boats">
  <form class="search-panel">
    <div class="mode-tabs">
      <div class="mode-tab"><svg width="20" height="20" viewBox="0 0 20 20"><path d="M2 11l7-2 3-7h2l-1 7 5 1v2l-5 1 1 5h-2l-3-5-7-1z" fill="#fff"/></svg>FLIGHTS</div>
      <div class="mode-tab"><svg width="20" height="20" viewBox="0 0 20 20"><rect x="5" y="2" width="10" height="16" fill="none" stroke="#fff" stroke-width="1.6"/><rect x="8" y="5" width="4" height="2" fill="#fff"/><rect x="8" y="9" width="4" height="2" fill="#fff"/></svg>HOTELS</div>
      <div class="mode-tab"><svg width="20" height="20" viewBox="0 0 20 20"><rect x="4" y="2" width="12" height="13" rx="3" fill="#fff"/><rect x="6" y="4" width="8" height="4" fill="#555"/><line x1="6" y1="15" x2="4" y2="19" stroke="#fff" stroke-width="1.6"/><line x1="14" y1="15" x2="16" y2="19" stroke="#fff" stroke-width="1.6"/></svg>TRAIN</div>
      <div class="mode-tab"><svg width="20" height="20" viewBox="0 0 20 20"><path d="M3 10l2-5h10l2 5v5H3z" fill="#fff"/><circle cx="6" cy="15" r="2" fill="#555"/><circle cx="14" cy="15" r="2" fill="#555"/></svg>CARS</div>
      <div class="mode-tab active"><svg width="20" height="20" viewBox="0 0 20 20"><rect x="3" y="6" width="14" height="11" rx="1" fill="#fff"/><rect x="7" y="3" width="6" height="4" fill="none" stroke="#fff" stroke-width="1.6"/></svg>PACKAGES</div>
    </div>
    <div class="sub-tabs">
      <div class="sub-tab active">FLIGHT + HOTEL</div>
      <div class="sub-tab">FLIGHT + HOTEL + CAR</div>
      <div class="sub-tab">FLIGHT + CAR</div>
      <div class="sub-tab">HOTEL + CAR</div>
    </div>

    <label class="field-label" style="left:18px;top:156px">FLYING FROM</label>
    <div class="field" style="left:18px;top:181px;width:365px"><svg width="12" height="14" viewBox="0 0 12 14"><path d="M6 1a4 4 0 014 4c0 3-4 8-4 8S2 8 2 5a4 4 0 014-4z" fill="#aaa"/></svg>City or Airport</div>
    <label class="field-label" style="left:401px;top:156px">FLYING TO</label>
    <div class="field" style="left:401px;top:181px;width:364px"><svg width="12" height="14" viewBox="0 0 12 14"><path d="M6 1a4 4 0 014 4c0 3-4 8-4 8S2 8 2 5a4 4 0 014-4z" fill="#aaa"/></svg>City or Airport</div>

    <label class="field-label" style="left:18px;top:230px">DEPARTING</label>
    <div class="field" style="left:18px;top:253px;width:202px"><svg width="12" height="12" viewBox="0 0 12 12"><rect x="1" y="2" width="10" height="9" fill="none" stroke="#aaa"/><line x1="1" y1="5" x2="11" y2="5" stroke="#aaa"/></svg>mm/dd/yyyy</div>
    <label class="field-label" style="left:229px;top:230px">RETURNING</label>
    <div class="field" style="left:229px;top:253px;width:201px"><svg width="12" height="12" viewBox="0 0 12 12"><rect x="1" y="2" width="10" height="9" fill="none" stroke="#aaa"/><line x1="1" y1="5" x2="11" y2="5" stroke="#aaa"/></svg>mm/dd/yyyy</div>
    <label class="field-label" style="left:439px;top:230px">ROOM</label>
    <div class="field select" style="left:439px;top:253px;width:98px">1</div>
    <label class="field-label" style="left:552px;top:230px">ADULTS(18+)</label>
    <div class="field select" style="left:552px;top:253px;width:96px">3</div>
    <label class="field-label" style="left:663px;top:230px">CHILDREN</label>
    <div class="field select" style="left:663px;top:253px;width:98px">2</div>

    <div class="check-row"><i></i>I ONLY NEED A HOTEL FOR PART OF MY STAY</div>
    <div class="advanced">ADVANCED OPTIONS ▴</div>
    <div class="field select" style="left:18px;top:369px;width:202px">Business</div>
    <div class="search-btn">SEARCH</div>
  </form>
</section>

<section class="welcome">
  <h2 class="section-title" style="top:714px">Welcome To <span>Our Company</span></h2>
  <p class="section-intro" style="top:764px">Plan every part of your journey in one place, from flights and hotels to visas, fees and local tips shared by travellers who have already been there and know the way.</p>

  <div class="feature" style="left:96px">
    <svg width="80" height="62" viewBox="0 0 80 62"><g fill="none" stroke="var(--orange)" stroke-width="3"><path d="M10 52V14M70 52V30M10 40h60M10 30h60"/><rect x="18" y="20" width="18" height="10" rx="3"/><rect x="42" y="20" width="18" height="10" rx="3"/></g></svg>
    <h3>Cozy &amp; Charming Rooms</h3>
    <p>Compare rooms, rates and reviews in minutes and book the stay that suits your plans, your budget and the way you like to travel.</p>
  </div>
  <div class="feature" style="left:440px">
    <svg width="80" height="62" viewBox="0 0 80 62"><circle cx="30" cy="20" r="9" fill="var(--green)"/><path d="M10 52l55-18" stroke="var(--green)" stroke-width="3"/><path d="M40 8l6 40" stroke="var(--orange)" stroke-width="3"/><path d="M28 12q18-10 36 6z" fill="var(--orange)"/></svg>
    <h3 style="color:var(--green)">Relax in a beautiful contest</h3>
    <p>Find quiet beaches, spa resorts and garden retreats chosen by other guests, with honest notes on prices and the best time to visit.</p>
  </div>
  <div class="feature" style="left:784px">
    <svg width="80" height="62" viewBox="0 0 80 62"><circle cx="52" cy="14" r="7" fill="var(--orange)"/><path d="M18 30l18-12 10 12" fill="none" stroke="var(--orange)" stroke-width="4"/><path d="M8 42q8-6 16 0t16 0 16 0 16 0M8 52q8-6 16 0t16 0 16 0 16 0" fill="none" stroke="var(--orange)" stroke-width="3"/></svg>
    <h3>Enjoy country side activities</h3>
    <p>Join hikes, farm visits, cycling routes and village markets, each one checked by locals and rated by travellers who tried them first.</p>
  </div>
</section>

<section class="destinations">
  <h2 class="section-title" style="top:40px">Our <span>Destinations</span></h2>
  <p class="section-intro" style="top:90px">Browse hand-picked places around the world with clear notes on entry rules, costs, seasons and the best ways to get around once you land at your chosen destination.</p>

  <article class="card" style="left:86px;top:163px;width:326px;height:390px">
    <div class="photo" style="height:190px;background:linear-gradient(135deg,#9bb7d8,#c98a63 60%,#6b8a4a)" role="img" aria-label="Group of friends taking a selfie outdoors"></div>
    <h4 style="top:218px">Contrary to popular</h4>
    <div class="stars" style="top:222px"><i class="on"></i><i class="on"></i><i class="on"></i><i class="on"></i><i></i></div>
    <p style="top:248px">Old streets, quiet harbours and warm evenings make this a favourite stop for first-time visitors and returning travellers alike, all year round.</p>
    <div class="meta" style="top:340px"><span>⚲ Locations</span><span>◷ 15 Days</span><span><b>$</b> 35.00</span></div>
  </article>
  <article class="card" style="left:438px;top:163px;width:316px;height:390px">
    <div class="photo" style="height:190px;background:linear-gradient(135deg,#7a8e6a,#a89a84 50%,#5a6e7a)" role="img" aria-label="Travellers riding elephants through a river"></div>
    <h4 style="top:218px">Contrary to popular</h4>
    <div class="stars" style="top:222px"><i class="on"></i><i class="on"></i><i class="on"></i><i class="on"></i><i></i></div>
    <p style="top:248px">Old streets, quiet harbours and warm evenings make this a favourite stop for first-time visitors and returning travellers alike, all year round.</p>
    <div class="meta" style="top:340px"><span>⚲ Locations</span><span>◷ 15 Days</span><span><b>$</b> 35.00</span></div>
  </article>
  <article class="card" style="left:786px;top:163px;width:326px;height:390px">
    <div class="photo" style="height:190px;background:linear-gradient(135deg,#f2d39a,#d49a5a 50%,#8a6a4a)" role="img" aria-label="Traveller photographing a city tower at sunset"></div>
    <h4 style="top:218px">Contrary to popular</h4>
    <div class="stars" style="top:222px"><i class="on"></i><i class="on"></i><i class="on"></i><i class="on"></i><i></i></div>
    <p style="top:248px">Old streets, quiet harbours and warm evenings make this a favourite stop for first-time visitors and returning travellers alike, all year round.</p>
    <div class="meta" style="top:340px"><span>⚲ Locations</span><span>◷ 15 Days</span><span><b>$</b> 35.00</span></div>
  </article>
</section>

<section class="banner" role="img" aria-label="Woman in a sun hat relaxing on a beach by the sea">
  <h3><span class="kicker">GREAT EXPERIENCES</span><span class="headline">FOR TRAVEL AND TOURISM</span></h3>
  <div class="tour-btn">TAKE YOUR TOUR</div>
</section>

<section class="guides">
  <h2 class="section-title" style="top:2130px">Tour <span>Guides</span></h2>
  <p class="section-intro" style="top:2180px">Meet local guides who know every street, market and viewpoint, and who will help you see more of each city than any map or guidebook ever could.</p>

  <article class="card" style="left:107px;top:2253px;width:296px;height:370px">
    <div class="photo" style="left:0;right:0;top:0;height:256px;background:linear-gradient(160deg,#c9d6dc,#8fa7b8 55%,#50708a)" role="img" aria-label="Smiling tour guide in a denim shirt"></div>
    <h4 style="top:272px;left:16px">Jaron Smeal</h4>
    <div class="stars" style="top:276px"><i class="on"></i><i class="on"></i><i class="on"></i><i class="on"></i><i></i></div>
    <p style="top:300px;left:16px">Born in the city, speaks four languages and loves showing guests the hidden corners.</p>
  </article>
  <article class="card" style="left:450px;top:2253px;width:296px;height:370px">
    <div class="photo" style="left:0;right:0;top:0;height:256px;background:linear-gradient(160deg,#d9cfc2,#b8a48e 55%,#7a6452)" role="img" aria-label="Tour guide holding a map in a city street"></div>
    <h4 style="top:272px;left:16px">Jaron Smeal</h4>
    <div class="stars" style="top:276px"><i class="on"></i><i class="on"></i><i class="on"></i><i class="on"></i><i></i></div>
    <p style="top:300px;left:16px">Born in the city, speaks four languages and loves showing guests the hidden corners.</p>
  </article>
  <article class="card" style="left:792px;top:2253px;width:296px;height:370px">
    <div class="photo" style="left:0;right:0;top:0;height:256px;background:linear-gradient(160deg,#cdd3d8,#8e9aa4 55%,#4e5e6e)" role="img" aria-label="Tour guide checking a phone outdoors"></div>
    <h4 style="top:272px;left:16px">Jaron Smeal</h4>
    <div class="stars" style="top:276px"><i class="on"></i><i class="on"></i><i class="on"></i><i class="on"></i><i></i></div>
    <p style="top:300px;left:16px">Born in the city, speaks four languages and loves showing guests the hidden corners.</p>
  </article>
</section>

<section class="testimonial">
  <span class="quote-mark" style="left:160px;top:2720px">“</span>
  <p class="quote">We planned our whole trip here, from the first flight to the last night in a small seaside hotel. The visa notes saved us hours, the fees were clear from the start and the local tips from other travellers led us to places we would never have found. Everything felt easy, and we are already choosing our next destination.</p>
  <span class="quote-mark" style="left:560px;top:2822px">”</span>
  <div class="quote-name">JARON SMEAL</div>
  <div class="quote-date">Posted On 07 January 2017</div>
  <div class="avatar" role="img" aria-label="Portrait of the reviewer"></div>
</section>

<section class="partners" aria-label="Partners">
  <div class="partner" style="left:90px"><i></i>Nexolite</div>
  <div class="partner" style="left:258px"><i></i>Varrow</div>
  <div class="partner" style="left:438px"><i></i>Tunebay</div>
  <div class="partner" style="left:618px"><i></i>Quadrix</div>
  <div class="partner" style="left:798px"><i></i>Corvane</div>
  <div class="partner" style="left:974px"><i></i>Pixelmoor</div>
</section>

<footer class="site-footer">
  <h5 style="left:95px">Quick Links</h5>
  <ul class="link-list" style="left:98px"><li>Home</li><li>Travel</li><li>Hotels</li><li>Cars</li><li>Flights</li><li>Contact</li></ul>

  <h5 style="left:276px">Contact Us</h5>
  <ul class="contact-list">
    <li><svg width="14" height="12" viewBox="0 0 14 12"><path d="M3 1l3 3-2 2q2 3 4 4l2-2 3 3-2 2Q4 11 1 3z" fill="#999"/></svg>(000)-121-1231 (Phone)</li>
    <li><svg width="14" height="12" viewBox="0 0 14 12"><rect x="1" y="3" width="12" height="8" fill="#999"/><rect x="4" y="0" width="6" height="4" fill="#bbb"/></svg>(000)-121-1231 (Fax)</li>
    <li><svg width="14" height="12" viewBox="0 0 14 12"><rect x="1" y="2" width="12" height="9" fill="none" stroke="#999"/><path d="M1 2l6 5 6-5" fill="none" stroke="#999"/></svg><a>info@rovanix.com</a></li>
    <li><svg width="14" height="14" viewBox="0 0 14 14"><path d="M7 1a4 4 0 014 4c0 3-4 8-4 8S3 8 3 5a4 4 0 014-4z" fill="#999"/></svg><span>70 Lorem Ipsum Dummy Text<br>Lorem Ipsum</span></li>
  </ul>

  <h5 style="left:546px">Resort Locations</h5>
  <ul class="link-list" style="left:546px"><li>Algarve holidays</li><li>Alicante car hire</li><li>Amsterdam flights</li><li>Bangkok flights</li><li>Benidorm holidays</li><li>Cuba holidays</li></ul>

  <h5 style="left:774px">Email Subscription</h5>
  <p class="subscribe-note">Register your email address to get information about us</p>
  <div class="subscribe"><div class="email">Email Address</div><div class="go">SUBSCRIBE</div></div>
  <h5 style="left:774px;top:3226px">Stay Connected</h5>
  <div class="social" aria-label="Social links"><i></i><i></i><i></i><i></i><i></i><i></i><i></i><i></i></div>

  <p class="copyright">Copyright © 2017 Rovanix. All Rights Reserved &nbsp;|&nbsp; Privacy Policy | Terms of Use | Feedback</p>
</footer>

</body>
</html>
```